Business Card Design Project

We are looking to redesign the logo, business card and stationary of one of our group companies - SOLARO SUPPLY HOUSE LLC.

The company specialises in industrial PVC and CPVC Piping systems. It is situated in the Middle East and the focus is purely in this region.

The logo work is already completed. The file is uploaded for the reference.

We are looking for a clean minimalistic design for the business card.

regards
Rohit
Updates

Hello Everyone!

Thanks for submitting your designs. 

Yet to find the right design. Probably the below links will give you guys some more idea on what we would like.

Minimalist design with some creativity.

Rohit

http://exampledesignfolio.com/inspiration/15-beautifully-minimal-business-cards

http://www.samplelayoutbase.com/2011/11/14/30-minimalist-business-card-design/

http://www.primepixelcraft.com/inspiration/minimal-business-cards/

Target Market(s)

Industrial users

Industry/Entity Type

Industrial

Requirements
Must have
• - Minimalistic design

- Back side of the card should include the manufacturer PIPEMARQ NORTHERN's decal. The file is upload for the reference

- Further information
Company Name:
SOLARO SUPPLY HOUSE LLC
Address:
PO Box 8152, Sharjah Industrial Area 4, Qarwan Road
Sharjah, United Arab Emirates
Telephone:
+971-6-5000-118
Fax:
+977-6-5000-119
Email:
mail@sshlexample.com

- FYI, Solaro Supply House LLC is the authorised distributor for PIPEMARQ NORTHERN in the UAE. For further information on pipemarq please visit the website www.pipemarq-example.ca

```html
<!DOCTYPE html>
<html lang="en">
<head>
<meta charset="utf-8">
<title>Solaro Supply House LLC – Business Card</title>
<link rel="stylesheet" href="https://fonts.googleapis.com/css2?family=Arimo:wght@700&display=swap">
<style>
  :root {
    --card-bg: #f4f5f6;
    --fitting-light: #eceef0;
    --fitting-mid: #dcdfe2;
    --title-blue: #3a7cc4;
    --contact-blue: #2a5ea8;
    --email-blue: #3c78c0;
    --address-grey: #6b6b6b;
    --mark-blue: #2f6db5;
  }
  * { margin: 0; padding: 0; box-sizing: border-box; }
  html, body {
    width: 1200px;
    height: 686px;
    overflow: hidden;
    background: var(--card-bg);
  }
  .card {
    position: relative;
    width: 1200px;
    height: 686px;
    overflow: hidden;
    font-family: "Arimo", Arial, sans-serif;
    font-weight: 700;
    background: var(--card-bg);
  }
  .card__backdrop {
    position: absolute;
    inset: 0;
    background:
      radial-gradient(ellipse 360px 300px at 930px 420px, var(--fitting-mid) 0%, var(--fitting-light) 55%, transparent 80%),
      radial-gradient(ellipse 300px 240px at 230px 560px, var(--fitting-mid) 0%, var(--fitting-light) 60%, transparent 85%),
      radial-gradient(ellipse 420px 260px at 480px 170px, var(--fitting-light) 0%, transparent 80%),
      var(--card-bg);
  }
  .company-name {
    position: absolute;
    top: 30px;
    left: 0;
    width: 100%;
    text-align: center;
    font-size: 63px;
    line-height: 78px;
    color: var(--title-blue);
    letter-spacing: 1px;
    text-shadow: 3px 4px 6px rgba(0, 0, 0, 0.28);
  }
  .phone-lines {
    position: absolute;
    left: 55px;
    top: 299px;
    font-size: 32px;
    line-height: 41px;
    color: var(--contact-blue);
  }
  .address {
    position: absolute;
    right: 40px;
    top: 278px;
    text-align: right;
    font-style: normal;
    font-size: 28.5px;
    line-height: 34.3px;
    color: var(--address-grey);
  }
  .brand-mark {
    position: absolute;
    top: 541px;
    left: 0;
    width: 100%;
    display: flex;
    justify-content: center;
    align-items: center;
    gap: 14px;
  }
  .brand-mark__square {
    width: 56px;
    height: 56px;
    background: var(--mark-blue);
  }
  .brand-mark__name {
    font-size: 22px;
    color: var(--mark-blue);
  }
  .email {
    position: absolute;
    top: 628px;
    left: 0;
    width: 100%;
    text-align: center;
    font-size: 25px;
    line-height: 32px;
    color: var(--email-blue);
  }
</style>
</head>
<body>
  <main class="card">
    <div class="card__backdrop" role="img" aria-label="Faint greyscale photograph of PVC pipe fittings filling the card background"></div>

    <h1 class="company-name">SOLARO SUPPLY<br>HOUSE LLC</h1>

    <div class="phone-lines">
      <p class="phone-lines__tel">Tel: +971-6-5000-118</p>
      <p class="phone-lines__fax">Fax: +977-6-5000-119</p>
    </div>

    <address class="address">
      PO Box 8152<br>
      Sharjah Industrial Area 4<br>
      Qarwan Road<br>
      Sharjah<br>
      United Arab Emirates
    </address>

    <div class="brand-mark">
      <span class="brand-mark__square"></span>
      <span class="brand-mark__name">Solaro Supply House</span>
    </div>

    <p class="email">Email: mail@sshlexample.com</p>
  </main>
</body>
</html>
```